Postcard Mail Out - Dwight

We are a real estate company. We need a post card to mail out to potential clients to try and sale their land. We will attached a couple of post cards that we like but we do not want to copy them completely. We do need to put the Equal Housing Opportunity and the Realtor logos with a disclosure saying not intended to solicit currently listed properties. The image below is what we had started working on. We would like to include something about farm land, timber, maybe a pond, something along those lines. The PDF Files attached are a flyer that was mailed out by another company that we do not want to copy completely. Attached also will be our company's Logo.

Requirements
Must have
• We do need to put the Equal Housing Opportunity and the Realtor logos with a disclosure saying not intended to solicit currently listed properties.<br/><br/>At Cobb Harlow Summit Realty, we are blessed to have one of the very best Rural Land Specialists available. Dwight has years of experience promoting and selling rural land properties. Dwight has earned the trust of many landowners, as he is so PASSIONATE in all regards to rural land, farms and ranches. He has made a wide range of landowners very happy throughout his years in Real Estate. Call him today and show him your property, and he will provide you with a free analysis and strategy to maximize the return on your property.
Nice to have
• A picture of Dwight has been added to use on the back of the post card with his phone and number. It would be nice to have a east Texas scenery picture behind him instead of an office.<br/><br/>Please include front and back of post card in your submission.
Should not have
• Should not have Marcus Thorne's information on the postcard. That post card was just to show what we was wanting. The agent we want listed is Dwight Fenwick and his phone number is (555)412-3086.

```html
<!DOCTYPE html>
<html lang="en">
<head>
<meta charset="utf-8">
<title>Land For Sale Postcard – Front and Back</title>
<link href="https://fonts.googleapis.com/css2?family=Exo+2:ital,wght@0,500;0,600;0,700;1,500;1,600;1,700&display=swap" rel="stylesheet">
<style>
  :root{
    --bg:#d7d7d7;
    --navy:#163a6e;
    --royal:#2f5ea8;
    --steel:#5f86c4;
    --sky:#6fc0e6;
    --bright:#1a90d8;
    --ink:#144a72;
    --paper:#ffffff;
  }
  *{box-sizing:border-box;margin:0;padding:0}
  html,body{width:1200px;height:696px;overflow:hidden;background:var(--bg)}
  body{font-family:"Exo 2",sans-serif;position:relative}
  .card{position:absolute;top:158px;width:570px;height:380px;background:var(--paper);overflow:hidden;box-shadow:0 6px 14px rgba(0,0,0,.22)}
  .card--back{left:20px}
  .card--front{left:610px}
  .card svg.frame{position:absolute;inset:0}

  /* back */
  .back-photo{position:absolute;inset:0;background:linear-gradient(180deg,#f4f4f4 0%,#dcdcdc 45%,#bdbdbd 70%,#d0d0d0 100%)}
  .deals{position:absolute;left:0;top:12px;width:330px;height:44px;color:#fff;text-align:center;font-weight:600;font-size:15px;line-height:18px;padding-top:4px}
  .benefits{position:absolute;left:22px;top:68px;width:290px;list-style:none;color:var(--ink);font-weight:700;font-style:italic;font-size:13px;line-height:16px}
  .benefits li{position:relative;padding-left:14px;margin-bottom:4px}
  .benefits li::before{content:"";position:absolute;left:0;top:4px;border-left:8px solid var(--steel);border-top:5px solid transparent;border-bottom:5px solid transparent}
  .agent{position:absolute;left:22px;top:168px;width:280px;color:var(--ink);font-size:12px;line-height:15px}
  .agent .agent-name{font-weight:700}
  .agent .agent-phone{font-weight:700;color:var(--bright)}
  .brand-small{position:absolute;left:36px;top:206px;display:flex;align-items:center;gap:7px;color:var(--ink);font-weight:700;font-size:14px}
  .brand-small .dot,.brand-large .dot{width:14px;height:14px;border-radius:50%;background:var(--ink)}
  .contact{position:absolute;left:36px;top:228px;width:210px;text-align:center;color:var(--ink);font-weight:600;font-size:12px;line-height:14px}
  .contact .address{font-size:9px;line-height:12px;margin-top:3px;font-style:italic}
  .compliance{position:absolute;left:22px;top:284px;width:258px;display:flex;align-items:center;gap:8px}
  .badge{flex:none;width:24px;height:24px;background:var(--ink)}
  .badge--round{border-radius:50%}
  .disclosure{font-size:8px;line-height:10px;color:var(--ink);font-style:italic}
  .website{position:absolute;left:18px;top:348px;color:#fff;font-weight:700;font-size:16px}
  .stamp{position:absolute;left:455px;top:30px;width:85px;height:72px;border:1.5px solid var(--navy)}

  /* front */
  .front-photo{position:absolute;left:0;top:0;width:570px;height:260px;background:linear-gradient(180deg,#c9a7b4 0%,#e2a792 22%,#7e7468 48%,#4a4744 75%,#6d6a5c 100%)}
  .brand-large{position:absolute;right:36px;top:240px;display:flex;align-items:center;gap:9px;color:var(--ink);font-weight:700;font-size:22px}
  .brand-large .dot{width:20px;height:20px}
  .offer{position:absolute;left:22px;right:22px;bottom:30px;display:flex;justify-content:space-between;align-items:baseline;gap:10px}
  .offer .headline{color:var(--bright);font-weight:700;font-size:38px;white-space:nowrap}
  .offer .phone{color:var(--ink);font-weight:700;font-size:26px;white-space:nowrap}
</style>
</head>
<body>

<section class="card card--back" aria-label="Postcard back">
  <div class="back-photo" role="img" aria-label="Faded grayscale photo of a rural cabin on open land"></div>
  <svg class="frame" viewBox="0 0 570 380" aria-hidden="true">
    <defs>
      <linearGradient id="bandBack" x1="0" x2="1">
        <stop offset="0" stop-color="#2f5ea8"/><stop offset=".6" stop-color="#163a6e"/><stop offset="1" stop-color="#2f5ea8"/>
      </linearGradient>
    </defs>
    <polygon points="0,0 330,0 270,380 0,380" fill="#fff"/>
    <polygon points="330,0 346,0 286,380 270,380" fill="#163a6e"/>
    <rect x="0" y="12" width="330" height="44" fill="url(#bandBack)"/>
    <polygon points="0,336 277,336 270,380 0,380" fill="url(#bandBack)"/>
    <g stroke="#163a6e" stroke-width="1.2">
      <line x1="360" y1="200" x2="545" y2="200"/>
      <line x1="360" y1="235" x2="545" y2="235"/>
      <line x1="360" y1="270" x2="545" y2="270"/>
      <line x1="360" y1="305" x2="545" y2="305"/>
    </g>
  </svg>
  <div class="stamp"></div>
  <h2 class="deals">We Deals in:<br>Farm Land, Timber, Pond</h2>
  <ul class="benefits">
    <li>We provide the highest level of trust and service.</li>
    <li>Identify the recreational value on your land.</li>
    <li>Reach qualified buyers and Investors across the nation.</li>
  </ul>
  <p class="agent">Rural Land Specialist: <span class="agent-name">Dwight Fenwick</span><br>Call today for a free analysis: <span class="agent-phone">(555) 412-3086</span></p>
  <div class="brand-small"><span class="dot"></span>Cobb Harlow Summit Realty</div>
  <div class="contact">
    <p>(555) 730-2214</p>
    <p class="address">Ridgeford, TX 75000. 48 W Oak St.<br>Ridgeford, TX 75000. Directions.</p>
  </div>
  <div class="compliance">
    <span class="badge" role="img" aria-label="Equal Housing Opportunity badge"></span>
    <span class="badge badge--round" role="img" aria-label="Realtor badge"></span>
    <p class="disclosure">Not intended to solicit properties currently listed with another broker.</p>
  </div>
  <p class="website">www.cobbharlowsummit.com</p>
</section>

<section class="card card--front" aria-label="Postcard front">
  <div class="front-photo" role="img" aria-label="Photo of a two-storey suburban house with gabled roof at dusk under a pink sky"></div>
  <svg class="frame" viewBox="0 0 570 380" aria-hidden="true">
    <defs>
      <linearGradient id="swoosh" x1="0" x2="1">
        <stop offset="0" stop-color="#163a6e"/><stop offset=".5" stop-color="#2f5ea8"/><stop offset="1" stop-color="#5f86c4"/>
      </linearGradient>
    </defs>
    <path d="M0,245 Q250,150 570,138 L570,160 Q260,175 0,282 Z" fill="url(#swoosh)"/>
    <path d="M0,282 Q260,175 570,160 L570,172 Q265,190 0,298 Z" fill="#6fc0e6"/>
    <path d="M0,298 Q265,190 570,172 L570,380 L0,380 Z" fill="#fff"/>
    <rect x="0" y="370" width="570" height="10" fill="url(#swoosh)"/>
  </svg>
  <div class="brand-large"><span class="dot"></span>Cobb Harlow Summit Realty</div>
  <div class="offer">
    <span class="headline">Land For Sale?</span>
    <span class="phone">(555) 730-2214</span>
  </div>
</section>

</body>
</html>
```